Financial Advisor Resource Firm needs business card design

Need business card design for company in Omaha NE called Meridale Circle. We provide resources to financial advisors....workshop programs, retirement analysis, and insurance planning. I would like to see designs that use grays, greens, black, and white colors. The final design should communicate 'collaboration' and be simple yet attractive to financial planning clients. I will attached our logo and another picture of a puzzle piece coming together. I would like the incorporate the puzzle picture somehow, maybe on the back somehow, with color or just the gray scale....OR, the picture be the front of the card with 'Meridale' definition on it (see upload) and then company logo, employee name, title, address on the back (see ppt uploaded). The following disclosure needs to be included somewhere- Advisory services offered through Stonebrook Assets, LLC.
Updates

I uploaded a svg and ai file of the logo

Target Market(s)

Financial planning clients and financial advisors....so pretty diverse age range of about 40-70.

Industry/Entity Type

Financial Planning

Contact Information for Business Card

Tobias L. Fenwright, MBA
Founder/President
5287 E. Larkin Road
Suite 230
Omaha, NE 68190
Phone- (402) 555-0147
Cell- (402) 555-0183
Fax- (402) 555-0129
email- tobias@meridaleplan.example
web address- www.meridaleplan.example

Colors
1b1b1b
474747
d3d3d3
ffffff
9bcb3c
abd036

Requirements
Must have
• Must include logo provided, must be 2 sided, and must have disclosure...all of these items listed in project description

```html
<!DOCTYPE html>
<html lang="en">
<head>
<meta charset="utf-8">
<title>Meridale Circle — Business Card</title>
<link rel="stylesheet" href="https://fonts.googleapis.com/css2?family=Arimo:wght@400;700&family=Tinos:wght@400;700&display=swap">
<style>
  :root {
    --ink: #1b1b1b;
    --charcoal: #262626;
    --graphite: #474747;
    --mist: #d3d3d3;
    --paper: #ffffff;
    --leaf: #9bcb3c;
    --lime: #abd036;
    --stage: #ececec;
  }
  * { box-sizing: border-box; margin: 0; padding: 0; }
  html, body { width: 1200px; height: 780px; overflow: hidden; }
  body {
    background: var(--stage);
    display: flex;
    align-items: center;
    justify-content: center;
    gap: 40px;
    font-family: "Arimo", Arial, sans-serif;
  }
  .card {
    width: 540px;
    height: 309px;
    border-radius: 16px;
    overflow: hidden;
    position: relative;
    box-shadow: 0 6px 18px rgba(0,0,0,0.18);
  }

  /* Front */
  .card-front { background: var(--paper); display: flex; flex-direction: column; }
  .front-brand {
    flex: 0 0 168px;
    background: linear-gradient(180deg, #ffffff, #f1f1f1);
    display: flex;
    align-items: center;
    justify-content: center;
    gap: 12px;
  }
  .accent-stripe { flex: 0 0 7px; background: var(--leaf); }
  .front-details {
    flex: 1;
    background: var(--charcoal);
    display: flex;
    justify-content: space-between;
    padding: 20px 26px 16px 30px;
    color: var(--paper);
    font-size: 12px;
    line-height: 1.45;
  }
  .brand-name {
    font-family: "Tinos", "Times New Roman", serif;
    font-weight: 400;
    letter-spacing: 1.5px;
    text-transform: uppercase;
    white-space: nowrap;
  }
  .front-brand .brand-name { color: var(--ink); font-size: 34px; }
  .brand-dot { width: 16px; height: 16px; border-radius: 50%; background: var(--leaf); flex: none; }

  .person-name {
    font-family: "Tinos", "Times New Roman", serif;
    font-size: 15px;
    text-transform: uppercase;
    letter-spacing: 0.5px;
  }
  .person-title { color: var(--leaf); font-size: 13px; margin-bottom: 7px; }
  .contact-line { display: flex; align-items: center; gap: 7px; white-space: nowrap; }
  .contact-line + .contact-line { margin-top: 3px; }
  .contact-icon { width: 14px; height: 14px; flex: none; }
  .address-block { align-self: flex-start; }
  .address-block .city { margin-bottom: 6px; }
  .highlight { color: var(--leaf); }

  /* Back */
  .card-back {
    background: radial-gradient(ellipse at 45% 40%, #2e2e2e, var(--ink) 75%);
    display: flex;
    align-items: center;
    justify-content: center;
    gap: 14px;
  }
  .card-back .brand-name { color: var(--paper); font-size: 38px; }
  .disclosure {
    position: absolute;
    left: 0;
    right: 0;
    bottom: 16px;
    text-align: center;
    color: var(--mist);
    font-size: 9.5px;
    letter-spacing: 0.3px;
  }
</style>
</head>
<body>

  <section class="card card-front" aria-label="Business card front">
    <div class="front-brand">
      <span class="brand-dot"></span>
      <span class="brand-name">Meridale Circle</span>
    </div>
    <div class="accent-stripe"></div>
    <div class="front-details">
      <div class="person-block">
        <p class="person-name">Tobias L. Fenwright, MBA</p>
        <p class="person-title">Founder/President</p>
        <p class="contact-line">
          <svg class="contact-icon" viewBox="0 0 14 14" aria-label="Phone"><circle cx="7" cy="7" r="6.3" fill="none" stroke="var(--leaf)" stroke-width="1.4"/><path d="M4.6 4.2c.4-.4.8-.3 1 .1l.5 1c.1.3 0 .5-.2.7l-.3.3c.4.8 1 1.4 1.8 1.8l.3-.3c.2-.2.4-.3.7-.2l1 .5c.4.2.5.6.1 1-.9.9-2.3.5-3.6-.8S3.7 5.1 4.6 4.2z" fill="var(--leaf)"/></svg>
          <span>(402) 555-0147</span>
        </p>
        <p class="contact-line">
          <svg class="contact-icon" viewBox="0 0 14 14" aria-label="Mobile"><circle cx="7" cy="7" r="6.3" fill="none" stroke="var(--leaf)" stroke-width="1.4"/><rect x="5" y="3.6" width="4" height="6.8" rx="0.7" fill="none" stroke="var(--leaf)" stroke-width="1.1"/></svg>
          <span>(402) 555-0183</span>
        </p>
        <p class="contact-line">
          <svg class="contact-icon" viewBox="0 0 14 14" aria-label="Fax"><circle cx="7" cy="7" r="7" fill="var(--leaf)"/><rect x="4" y="5.5" width="6" height="4" rx="0.5" fill="var(--charcoal)"/><rect x="5" y="3.5" width="4" height="2" fill="var(--charcoal)"/></svg>
          <span>(402) 555-0129</span>
        </p>
      </div>
      <div class="address-block">
        <p class="street">5287 E. Larkin Road, Suite 230</p>
        <p class="city">Omaha, NE 68190</p>
        <p class="contact-line">
          <svg class="contact-icon" viewBox="0 0 14 14" aria-label="Email"><circle cx="7" cy="7" r="7" fill="var(--leaf)"/><rect x="3.6" y="4.6" width="6.8" height="4.8" fill="var(--charcoal)"/><path d="M3.8 4.8 7 7.3l3.2-2.5" fill="none" stroke="var(--leaf)" stroke-width="0.9"/></svg>
          <span>tobias@meridaleplan.example</span>
        </p>
        <p class="contact-line">
          <svg class="contact-icon" viewBox="0 0 14 14" aria-label="Website"><circle cx="7" cy="7" r="7" fill="var(--leaf)"/><circle cx="7" cy="7" r="3.6" fill="none" stroke="var(--charcoal)" stroke-width="1"/><path d="M3.4 7h7.2M7 3.4v7.2" stroke="var(--charcoal)" stroke-width="0.9"/></svg>
          <span>www.<span class="highlight">meridaleplan</span>.example</span>
        </p>
      </div>
    </div>
  </section>

  <section class="card card-back" aria-label="Business card back">
    <span class="brand-dot"></span>
    <span class="brand-name">Meridale Circle</span>
    <p class="disclosure">Advisory services offered through Stonebrook Assets, LLC</p>
  </section>

</body>
</html>
```